Website for "Nodo de Soluciones Verdantes"

We need a new web design for an enterprise dedicated to environment and energy saving engineering, based in Monterrey, Mexico.
They offer consulting services, mainly to enhance building designs, and they are also resellers for several products in the energy saving field.

The final design should be oriented to engineers and architects, and should communicate professionalism, innovation, environment care.

Here is the website of a partner enterprise, which does pretty much the same:

http://www.cirelumen.com/

Target Market(s)

mainly architects and engineers looking for solutions on energy efficiency building

Industry/Entity Type

Environment

Requirements
Must have
• Entry page must be quite graphical and intuitive, must have a "products listing" and a "projects portfolio".

```html
<!DOCTYPE html>
<html lang="en">
<head>
<meta charset="utf-8">
<title>Nodo de Soluciones Verdantes</title>
<link href="https://fonts.googleapis.com/css2?family=Oswald:wght@300;400&family=Roboto:wght@400&display=swap" rel="stylesheet">
<style>
:root{
  --purple:#4b4a8c;
  --green:#8cb624;
  --red:#e8452a;
  --text:#6b6b6b;
  --rule-light:#e4e4e4;
  --white:#ffffff;
}
*{margin:0;padding:0;box-sizing:border-box}
html,body{width:923px;height:1200px;overflow:hidden;background:var(--white)}
body{position:relative;font-family:"Roboto",Arial,sans-serif;color:var(--text)}
.abs{position:absolute}
.top-band{left:0;top:0;width:923px;height:5px;background:var(--purple)}
.brand{left:92px;top:22px;display:flex;align-items:center;gap:10px}
.brand-mark{width:44px;height:44px;border-radius:50%;background:var(--green)}
.brand-name{font-family:"Oswald",sans-serif;font-weight:400;font-size:17px;line-height:20px;color:var(--purple);width:170px}
.call{right:93px;top:18px;font-family:"Oswald",sans-serif;font-size:14px;color:var(--red)}
.call span{color:var(--purple)}
.search{left:608px;top:53px;width:222px;height:29px;border:1px solid #ddd}
.search-btn{position:absolute;right:0;top:4px;width:30px;height:20px;border-left:1px solid #ccc}
.nav{left:92px;top:95px;width:738px;height:33px;background:var(--green);display:flex}
.nav a{font-family:"Oswald",sans-serif;font-size:16px;color:var(--white);text-decoration:none;line-height:33px;text-transform:uppercase;position:absolute;top:0}
.nav .home{left:0;width:76px;height:33px;background:var(--red);text-align:center}
.hero{left:92px;top:139px;width:738px;height:292px;background:linear-gradient(180deg,#7fa9cf 0%,#c9d9e6 45%,#dde6ea 60%,#6f8a4e 85%,#3f5a2c 100%)}
.hero-caption{left:93px;top:258px;width:281px;height:60px;background:var(--green);padding:8px 13px;font-family:"Oswald",sans-serif;font-size:20px;line-height:22px;color:var(--white);text-transform:uppercase}
.dots{left:106px;top:412px;display:flex;gap:2px}
.dots i{width:11px;height:11px;border-radius:50%;background:#111;display:block}
.dots i.on{background:var(--green);border:1px solid #222}
.section-title{font-family:"Oswald",sans-serif;font-weight:300;font-size:17px;color:#333;text-transform:uppercase}
.rule{height:2px;background:var(--purple)}
.rule-light{height:2px;background:var(--rule-light)}
.arrows{display:flex;gap:3px}
.arrows i{width:12px;height:12px;background:var(--red);display:block;position:relative}
.arrows svg{position:absolute;left:3px;top:2px}
.card{width:170px}
.card .photo{width:170px;height:93px}
.card h3{font-family:"Oswald",sans-serif;font-weight:400;font-size:12px;color:var(--red);text-transform:uppercase;margin-top:7px}
.card p{font-size:8.5px;line-height:13px;text-align:justify;margin-top:3px}
.btn{display:inline-block;background:var(--green);color:var(--white);font-family:"Oswald",sans-serif;font-size:9px;width:48px;height:19px;line-height:19px;text-align:center;text-transform:uppercase}
.col-text p{font-size:8.5px;line-height:13px;text-align:justify}
.col-text p.lead{color:var(--green);font-size:9.5px;line-height:13px;margin-bottom:13px}
.footer{left:0;top:1142px;width:923px;height:58px;background:var(--purple)}
.footer p{position:absolute;left:92px;top:23px;font-size:9px;color:#e6e6f2}
.social{position:absolute;left:698px;top:20px;display:flex;gap:6px}
.social i{width:17px;height:17px;border-radius:4px;display:block}
</style>
</head>
<body>
<div class="abs top-band"></div>

<header>
  <div class="abs brand">
    <div class="brand-mark"></div>
    <div class="brand-name">Nodo de Soluciones Verdantes</div>
  </div>
  <div class="abs call">CALL US NOEW! <span>(000) 000 0000</span></div>
  <div class="abs search">
    <div class="search-btn">
      <svg width="30" height="20" viewBox="0 0 30 20"><circle cx="14" cy="9" r="3.5" fill="none" stroke="#555" stroke-width="1.4"/><line x1="16.5" y1="11.5" x2="19.5" y2="14.5" stroke="#555" stroke-width="1.8"/></svg>
    </div>
  </div>
  <nav class="abs nav">
    <a class="home" href="#">Home</a>
    <a href="#" style="left:98px">About Us</a>
    <a href="#" style="left:201px">Services</a>
    <a href="#" style="left:298px">Products</a>
    <a href="#" style="left:404px">News</a>
    <a href="#" style="left:479px">FAQ</a>
    <a href="#" style="left:545px">Testimonials</a>
    <a href="#" style="left:669px">Contact</a>
  </nav>
</header>

<section>
  <div class="abs hero" role="img" aria-label="Wind turbines shaped like plants against a cloudy sky with cooling towers"></div>
  <div class="abs hero-caption">Environment and energy saving engineering.</div>
  <div class="abs dots"><i></i><i></i><i class="on"></i></div>
</section>

<section>
  <h2 class="abs section-title" style="left:92px;top:447px">Product Listing</h2>
  <div class="abs arrows" style="left:803px;top:447px">
    <i><svg width="6" height="8"><path d="M5 0L1 4L5 8" fill="none" stroke="#fff" stroke-width="1.5"/></svg></i>
    <i><svg width="6" height="8"><path d="M1 0L5 4L1 8" fill="none" stroke="#fff" stroke-width="1.5"/></svg></i>
  </div>
  <div class="abs rule" style="left:92px;top:475px;width:738px"></div>

  <article class="abs card" style="left:92px;top:489px">
    <div class="photo" role="img" aria-label="White lamp figure on blue background" style="background:linear-gradient(135deg,#1f3f86,#4a6eb8)"></div>
    <h3>Energy saving products</h3>
    <p>At vero eos et accusamus et iusto odio dignissimos ducimus qui blanditiis praesentium voluptatum deleniti</p>
    <span class="btn" style="margin-top:8px">More info</span>
  </article>
  <article class="abs card" style="left:282px;top:489px">
    <div class="photo" role="img" aria-label="Light bulb hanging on turquoise background" style="background:linear-gradient(135deg,#3bb5c2,#8fd8de)"></div>
    <h3>Energy saving products</h3>
    <p>At vero eos et accusamus et iusto odio dignissimos ducimus qui blanditiis praesentium voluptatum deleniti</p>
    <span class="btn" style="margin-top:8px">More info</span>
  </article>
  <article class="abs card" style="left:470px;top:489px">
    <div class="photo" role="img" aria-label="Compact fluorescent bulb against a grey wall" style="background:linear-gradient(135deg,#7d87a8,#a8b0c8)"></div>
    <h3>Energy saving products</h3>
    <p>At vero eos et accusamus et iusto odio dignissimos ducimus qui blanditiis praesentium voluptatum deleniti</p>
    <span class="btn" style="margin-top:8px">More info</span>
  </article>
  <article class="abs card" style="left:659px;top:489px">
    <div class="photo" role="img" aria-label="Green spiral bulb illustration" style="background:linear-gradient(135deg,#dcdcd8,#c5d88a)"></div>
    <h3>Energy saving products</h3>
    <p>At vero eos et accusamus et iusto odio dignissimos ducimus qui blanditiis praesentium voluptatum deleniti</p>
    <span class="btn" style="margin-top:8px">More info</span>
  </article>

  <div class="abs rule-light" style="left:92px;top:686px;width:738px"></div>
</section>

<section>
  <h2 class="abs section-title" style="left:92px;top:700px">Welcome to Nodo !</h2>
  <div class="abs rule" style="left:92px;top:730px;width:485px"></div>
  <div class="abs" role="img" aria-label="Hand inserting a coin into a light switch" style="left:92px;top:754px;width:170px;height:136px;background:linear-gradient(135deg,#e2e4e6,#b8bcc0)"></div>
  <div class="abs col-text" style="left:274px;top:751px;width:301px">
    <p class="lead">At vero eos et accusamus et iusto odio dignissimos ducimus qui blanditiis praesentium voluptatum deleniti</p>
    <p>At vero eos et accusamus et iusto odio dignissimos ducimus qui blanditiis praesentium voluptatum deleniti Nam libero tempore, cum soluta nobis est eligendi optio cumque nihil impedit quo minus id quod maxime placeat facere possimus, omnis voluptas assumenda est, omnis dolor repellendus. Temporibus autem quibusdam et aut officiis debitis aut rerum necessitatibus saepe eveniet ut et voluptates repudiandae sint et molestiae non recusandae. Itaque earum rerum hic tenetur a sapiente delectus, ut aut reiciendis voluptatibus maiores</p>
  </div>

  <h2 class="abs section-title" style="left:601px;top:700px">Our Services</h2>
  <div class="abs rule" style="left:601px;top:730px;width:229px"></div>
  <div class="abs col-text" style="left:600px;top:751px;width:230px">
    <p class="lead">At vero eos et accusamus et iusto odio dignissimos ducimus qui blanditiis praesentium voluptatum deleniti</p>
    <p>At vero eos et accusamus et iusto odio dignissimos ducimus qui blanditiis praesentium voluptatum deleniti Nam libero tempore, cum soluta nobis est eligendi optio cumque nihil impedit quo minus id quod maxime placeat facere possimus, omnis voluptas assumenda est, omnis dolor repellendus. Temporibus autem quibusdam et aut officiis debitis aut rerum necessitatibus saepe eveniet ut</p>
  </div>

  <div class="abs rule-light" style="left:92px;top:914px;width:738px"></div>
</section>

<section>
  <h2 class="abs section-title" style="left:92px;top:928px">Projects Portfolio</h2>
  <div class="abs arrows" style="left:803px;top:930px">
    <i><svg width="6" height="8"><path d="M5 0L1 4L5 8" fill="none" stroke="#fff" stroke-width="1.5"/></svg></i>
    <i><svg width="6" height="8"><path d="M1 0L5 4L1 8" fill="none" stroke="#fff" stroke-width="1.5"/></svg></i>
  </div>
  <div class="abs rule" style="left:92px;top:958px;width:738px"></div>

  <article class="abs card" style="left:92px;top:972px">
    <div class="photo" role="img" aria-label="Bulb made of green leaves" style="background:linear-gradient(135deg,#f2f5f2,#9cc26a)"></div>
    <h3>Energy saving projects</h3>
    <span class="btn" style="margin-top:5px">More info</span>
  </article>
  <article class="abs card" style="left:282px;top:972px">
    <div class="photo" role="img" aria-label="Glass bulb with a small green island inside" style="background:linear-gradient(135deg,#1c6fa8,#63b1dc)"></div>
    <h3>Energy saving projects</h3>
    <span class="btn" style="margin-top:5px">More info</span>
  </article>
  <article class="abs card" style="left:470px;top:972px">
    <div class="photo" role="img" aria-label="Hands holding light bulbs on green background" style="background:linear-gradient(135deg,#1f5a24,#5a9c3a)"></div>
    <h3>Energy saving projects</h3>
    <span class="btn" style="margin-top:5px">More info</span>
  </article>
  <article class="abs card" style="left:659px;top:972px">
    <div class="photo" role="img" aria-label="Green globe with a power plug" style="background:linear-gradient(135deg,#4e9a2e,#b9dc7a)"></div>
    <h3>Energy saving projects</h3>
    <span class="btn" style="margin-top:5px">More info</span>
  </article>
</section>

<footer class="abs footer">
  <p>© 2013 Nodo Verdante | All Rights Reserved.</p>
  <div class="social" aria-label="Social links">
    <i style="background:#2f7ad6"></i>
    <i style="background:#35b0e6"></i>
    <i style="background:#1e89c8"></i>
    <i style="background:#d9452b"></i>
    <i style="background:#d6342c"></i>
    <i style="background:#cf2f3a"></i>
  </div>
</footer>
</body>
</html>
```